Yard sign design for high end luxury home builder.

Need a design for signage on custom homes that are being built. I already have a logo that I am satisfied with that needs to be incorporated. I need the following incorporated in the design of the sign-
- Lic number 381526
- phone number (805) 555-0148‬
- quennbuilderscrew.com
- Logo/Branding

If possible it may be nice to have the following quote that is on are business cards-

Quote from Gerard of Norvelle-
HE WHO WORKS WITH HIS HANDS IS A LABORER.
HE WHO WORKS WITH HIS HANDS & HIS HEAD IS A CRAFTSMAN.
HE WHO WORKS WITH HIS HANDS & HIS HEAD & HIS HEART IS AN ARTISAN.
-GERARD OF NORVELLE

Target Market(s)

Archetect, Designers, Clients desiring to build a new home or remodel.

Colors
fde9d4
fee4d5
fabb94
fac994
faa54b
f68d4d
f37122
f78f20
f68e4e

Requirements
Must have
• - Lic number 381526
• - phone number (805) 555-0148‬
• - quennbuilderscrew.com
• - Logo/Branding
Nice to have
• Quote from Gerard of Norvelle-
• HE WHO WORKS WITH HIS HANDS IS A LABORER.
• HE WHO WORKS WITH HIS HANDS & HIS HEAD IS A CRAFTSMAN.
• HE WHO WORKS WITH HIS HANDS & HIS HEAD & HIS HEART IS AN ARTISAN.
• -GERARD OF NORVELLE
• OR the below statement-
• Craftsmen that Care
Should not have
• Any additional verbiage not specified above including any type of verbiage about what kind of company we are. For instance- Integrity, reputable... It's just all played out. Im just looking for a bitching design that has the info that compliments my logo/branding.

```html
<!DOCTYPE html>
<html lang="en">
<head>
<meta charset="utf-8">
<title>Quenn Builders Crew – Yard Sign</title>
<link rel="stylesheet" href="https://fonts.googleapis.com/css2?family=Barlow:wght@600;700;800&display=swap">
<style>
  :root {
    --page: #ecebe8;
    --white: #ffffff;
    --ink: #1d1b19;
    --tan: #a8916f;
    --tan-banner: #ad9675;
    --wood-dark: #3f2818;
    --wood-mid: #5a3a24;
    --wood-light: #6b4a30;
    --text-light: #ffffff;
  }
  * { margin: 0; padding: 0; box-sizing: border-box; }
  html, body { width: 1200px; height: 1200px; overflow: hidden; background: var(--page); }
  body { position: relative; font-family: "Barlow", Arial, sans-serif; }

  .yard-sign {
    position: absolute; left: 40px; top: 178px;
    width: 1120px; height: 843px;
    background: var(--white); overflow: hidden;
    box-shadow: 0 6px 18px rgba(0,0,0,0.18);
  }
  .craft-photo {
    position: absolute; left: 400px; top: 0; width: 720px; height: 430px;
    background:
      linear-gradient(90deg, var(--white) 0%, rgba(255,255,255,0.85) 25%, rgba(255,255,255,0.35) 60%, rgba(255,255,255,0.1) 100%),
      linear-gradient(160deg, #d9c3a4 0%, #b8946e 45%, #8c6a4b 100%);
  }
  .wood-panel {
    position: absolute; left: 0; top: 415px; width: 1120px; height: 428px;
    background: linear-gradient(180deg, var(--wood-mid) 0%, var(--wood-light) 40%, var(--wood-dark) 100%);
  }

  .brand {
    position: absolute; left: 70px; top: 40px; width: 310px;
    display: flex; flex-direction: column; align-items: center;
    color: var(--tan); font-weight: 800; text-transform: uppercase;
  }
  .brand-square { width: 150px; height: 150px; background: var(--tan); margin-bottom: 26px; }
  .brand-name { font-size: 104px; line-height: 0.9; letter-spacing: 4px; }
  .brand-sub { font-size: 27px; letter-spacing: 3px; margin-top: 6px; }

  .quote {
    position: absolute; left: 425px; width: 645px; top: 118px;
    text-align: center; color: var(--ink);
  }
  .quote-line { font-weight: 700; font-size: 52px; line-height: 68px; letter-spacing: -0.5px; }
  .quote-author {
    display: flex; align-items: center; gap: 10px; margin-top: 14px;
    font-weight: 700; font-size: 22px;
  }
  .quote-author::before, .quote-author::after {
    content: ""; flex: 1; height: 2px; background: var(--ink);
  }

  .tagline {
    position: absolute; left: 72px; top: 415px; width: 976px; height: 89px;
    background: var(--tan-banner);
    clip-path: polygon(0 0, 100% 0, 98.5% 100%, 1.5% 100%);
    display: flex; align-items: center; justify-content: center;
    color: var(--ink); font-weight: 800; font-size: 64px; letter-spacing: 0.5px;
  }
  .contact { position: absolute; left: 0; width: 100%; text-align: center; color: var(--text-light); font-weight: 700; }
  .licence { top: 522px; font-size: 62px; }
  .phone { top: 600px; font-size: 104px; }
  .website { top: 720px; font-size: 68px; }
</style>
</head>
<body>
  <main class="yard-sign">
    <div class="craft-photo" role="img" aria-label="Photo of hands carving wood at a workbench with hand tools"></div>
    <div class="wood-panel" role="img" aria-label="Dark weathered wood plank texture"></div>

    <div class="brand">
      <div class="brand-square"></div>
      <div class="brand-name">Quenn</div>
      <div class="brand-sub">Builders Crew</div>
    </div>

    <div class="quote">
      <p class="quote-line">HE WHO WORKS WITH</p>
      <p class="quote-line">HIS HANDS IS A LABORER.</p>
      <p class="quote-author">GERARD OF NORVELLE</p>
    </div>

    <div class="tagline">CRAFTSMEN THAT CARE</div>
    <p class="contact licence">LIC # 381526</p>
    <p class="contact phone">PH: (805) 555-0148</p>
    <p class="contact website">QUENNBUILDERSCREW.COM</p>
  </main>
</body>
</html>
```